Animal Eye Clinic needs a Business card

We are a new veterinary ophthalmology practice (Ridgeline Pet Vision Care) and we need a business card designed. We only see animal eyes - we are not a regular veterinary clinic. We already have a logo. We are looking for a professional, good looking business card to hand out to our clients. We are looking for something simple but professional and contemporary. Our logo is likely the only picture/graphic that needs to be on the card.
Updates

Contact Information for Business Card

Delia Vossman, BSc, DVM, MSc, DipACVO
Veterinary Ophthalmologist

Phone: 250.418.3927
Email: ridgelinepetvisioncare@mailbox-example.net
Website: ridgelinepetvisioncare-example.net
Address: 1874 Thornbury Rd
Kelowna, BC, V1X 4M9

Colors

Designer to choose colors to be used in the design.

Requirements
Must have
• Our logo (attached)

```html
<!DOCTYPE html>
<html lang="en">
<head>
<meta charset="utf-8">
<title>Ridgeline Pet Vision Care – Business Card</title>
<link href="https://fonts.googleapis.com/css2?family=Arimo:wght@400;700&display=swap" rel="stylesheet">
<style>
  :root {
    --backdrop: #2b2d31;
    --card: #1e2225;
    --card-edge: #272c30;
    --teal: #1b9db3;
    --silver: #a9adb1;
    --ink-light: #e6e8ea;
  }
  * { margin: 0; padding: 0; box-sizing: border-box; }
  html, body {
    width: 1200px; height: 800px; overflow: hidden;
    background: var(--backdrop);
    font-family: "Arimo", Arial, sans-serif;
  }
  .canvas { position: relative; width: 1200px; height: 800px; }
  .card {
    position: absolute; width: 525px; height: 300px;
    background: var(--card);
    border: 1px solid var(--card-edge);
    box-shadow: 0 18px 40px rgba(0,0,0,0.45);
  }
  .card-front { left: 80px; top: 70px; display: flex; align-items: center; justify-content: center; }
  .card-back { left: 595px; top: 430px; }

  .brand { display: flex; align-items: center; gap: 14px; }
  .brand-dot { width: 46px; height: 46px; border-radius: 50%; background: var(--silver); flex: none; }
  .brand-name {
    font-weight: 700; text-transform: uppercase; line-height: 1.15;
    letter-spacing: 0.12em;
  }
  .card-front .brand-name { color: var(--silver); font-size: 22px; }
  .card-back .brand-name { color: var(--teal); font-size: 16px; }
  .card-back .brand-dot { width: 30px; height: 30px; background: var(--teal); }

  .back-content { position: absolute; left: 40px; top: 34px; right: 30px; }
  .person { color: var(--teal); font-size: 19px; }
  .person-name { font-weight: 700; }
  .person-role { color: var(--ink-light); font-size: 13px; margin-top: 3px; }
  .address { color: var(--ink-light); font-size: 13px; line-height: 1.35; margin-top: 20px; }
  .contacts { list-style: none; margin-top: 14px; }
  .contacts li {
    display: flex; align-items: center; gap: 8px;
    color: var(--ink-light); font-size: 12.5px; line-height: 1.6;
  }
  .contact-icon { width: 14px; height: 14px; flex: none; }
  .card-back .brand { position: absolute; left: 40px; bottom: 26px; gap: 10px; }
</style>
</head>
<body>
<main class="canvas">
  <section class="card card-front" aria-label="Card front">
    <div class="brand">
      <span class="brand-dot"></span>
      <div class="brand-name">Ridgeline<br>Pet Vision Care</div>
    </div>
  </section>

  <section class="card card-back" aria-label="Card back">
    <div class="back-content">
      <p class="person"><span class="person-name">Delia Vossman</span>, BSc, DVM, MSc, DipACVO</p>
      <p class="person-role">Veterinary Ophthalmologist</p>
      <p class="address">1874 Thornbury Rd<br>Kelowna, BC, V1X 4M9</p>
      <ul class="contacts">
        <li>
          <svg class="contact-icon" viewBox="0 0 14 14" aria-hidden="true"><circle cx="7" cy="7" r="7" fill="#1b9db3"/><path d="M4.3 3.6c.4-.3.9-.2 1.1.2l.6 1.1c.2.4 0 .7-.3.9l-.3.2c.4.9 1.1 1.6 2 2l.2-.3c.2-.3.6-.4.9-.3l1.1.6c.4.2.5.7.2 1.1-.5.7-1.3.9-2.1.6C6.1 9.1 4.9 7.9 4.1 6.3c-.3-.8-.1-1.9.2-2.7z" fill="#1e2225"/></svg>
          250.418.3927
        </li>
        <li>
          <svg class="contact-icon" viewBox="0 0 14 14" aria-hidden="true"><circle cx="7" cy="7" r="7" fill="#1b9db3"/><rect x="3.5" y="4.5" width="7" height="5" rx=".6" fill="#1e2225"/><path d="M3.8 4.9 7 7.3l3.2-2.4" stroke="#1b9db3" stroke-width=".8" fill="none"/></svg>
          ridgelinepetvisioncare@mailbox-example.net
        </li>
        <li>
          <svg class="contact-icon" viewBox="0 0 14 14" aria-hidden="true"><circle cx="7" cy="7" r="7" fill="#1b9db3"/><circle cx="7" cy="7" r="3.6" fill="none" stroke="#1e2225" stroke-width=".9"/><ellipse cx="7" cy="7" rx="1.5" ry="3.6" fill="none" stroke="#1e2225" stroke-width=".9"/><path d="M3.4 7h7.2" stroke="#1e2225" stroke-width=".9"/></svg>
          ridgelinepetvisioncare-example.net
        </li>
      </ul>
    </div>
    <div class="brand">
      <span class="brand-dot"></span>
      <div class="brand-name">Ridgeline<br>Pet Vision Care</div>
    </div>
  </section>
</main>
</body>
</html>
```